Fenwick Grading LTD - website for irrigation & Landscape Lighting & Buried service wire

Looking for a website to help promote my business with Irrigation (installation, service, etc) and buried service wire/drainage solutions.

Commercial/Residential

Landscape lighting.

I’ll get photos in the trucks and trailers to upload as well maybe the machine as well.

Target Market(s)

Homeowners who want green grass and beautiful gardens. Beautiful landscape lighting

Industry/Entity Type

Irrigation systems and landscape lighting and buried service wire to homes and offering Drainage soltions.

Coding

Coded - Design and coding required

Number of Pages Required

4 page

Colors
F0912C
F2A743
F7CA91
FBE8D2
FDF5EE

Requirements
Must have
• was hoping to link up my email on fenwickgrading@mailbox-example.net with the website if possible.
Nice to have
• Page for Irrigation, page for landscape lighting, page buried service wire & drainage soltions.

```html
<!DOCTYPE html>
<html lang="en">
<head>
<meta charset="utf-8">
<title>Fenwick Grading LTD — Irrigation &amp; Landscape Lighting</title>
<link href="https://fonts.googleapis.com/css2?family=Montserrat:wght@400;500;600;700&family=Lato:wght@400;700&display=swap" rel="stylesheet">
<style>
:root{
  --orange:#F0912C;
  --orange-2:#F2A743;
  --orange-3:#F7CA91;
  --orange-4:#FBE8D2;
  --cream:#FDF5EE;
  --grey-band:#8a8a8a;
  --heading-grey:#6b6b6b;
  --text:#3a3a3a;
  --soft:#f4f4f4;
  --dark:#333333;
  --white:#ffffff;
}
*{box-sizing:border-box;margin:0;padding:0}
html,body{width:1200px;height:4254px;overflow:hidden}
body{position:relative;background:var(--white);font-family:"Lato",sans-serif;color:var(--text)}
.abs{position:absolute}
.head-font{font-family:"Montserrat",sans-serif}

/* top bar + header */
.topbar{left:0;top:0;width:1200px;height:10px;background:linear-gradient(90deg,var(--grey-band) 50%,var(--orange) 50%)}
.brand{left:50px;top:52px;width:170px;font-family:"Montserrat",sans-serif;font-weight:700;font-size:21px;line-height:26px;color:var(--orange);text-transform:uppercase;display:flex;gap:10px;align-items:center}
.brand-mark{width:14px;height:14px;background:var(--orange);flex:none}
.nav{top:74px;font-family:"Montserrat",sans-serif;font-size:13.5px;font-weight:500;color:#222;letter-spacing:.3px}
.phone-badge{left:894px;top:51px;width:62px;height:62px;border-radius:50%;background:linear-gradient(135deg,var(--orange),#a8744a);display:flex;align-items:center;justify-content:center}
.phone-label{left:972px;top:58px;font-family:"Montserrat",sans-serif;font-size:14px;font-weight:600;color:#222}
.phone-number{left:972px;top:84px;font-family:"Montserrat",sans-serif;font-size:19px;font-weight:700;color:#111}

/* hero */
.hero-photo{left:0;top:152px;width:1200px;height:620px;
  background:linear-gradient(180deg,#000 0%,#0a0d06 35%,#2a3a10 55%,#5a3a22 78%,#7a5032 100%);
  clip-path:polygon(0 0,100% 0,100% 67%,50% 100%,0 67%)}
.hero-title{left:0;top:226px;width:1200px;text-align:center;font-family:"Montserrat",sans-serif;font-weight:700;font-size:27px;line-height:51px;color:var(--white);letter-spacing:.5px}
.hl{color:var(--orange)}

/* buttons */
.btn{display:flex;align-items:center;justify-content:flex-end;padding-right:22px;font-family:"Montserrat",sans-serif;font-weight:700;font-size:19px;color:var(--white);letter-spacing:.4px;
  background:linear-gradient(90deg,#8d8d8d 0%,#b98a5c 40%,var(--orange) 100%);
  clip-path:polygon(0 0,100% 0,100% 100%,12% 100%);box-shadow:0 3px 6px rgba(0,0,0,.3)}
.btn::before{content:"";position:absolute;left:26%;top:50%;width:14px;height:14px;margin-top:-7px;background:var(--white)}
.btn-light{background:var(--white);color:var(--orange);clip-path:polygon(0 0,100% 0,100% 100%,18% 100%)}
.btn-light::before{background:var(--orange)}

.section-mark{width:14px;height:14px;background:var(--orange)}

/* about */
.about-photo{left:110px;top:913px;width:448px;height:465px;
  background:linear-gradient(180deg,#2f6fc4 0%,#8fb6e0 25%,#8a5a3a 55%,#3f4a2a 80%,#777 100%);
  clip-path:polygon(0 0,100% 0,50% 100%)}
.section-title{font-family:"Montserrat",sans-serif;font-weight:700;font-size:34px;letter-spacing:.5px;color:var(--heading-grey)}
.section-title .hl{color:var(--orange)}
.about-copy{left:599px;top:962px;width:492px;font-size:14px;line-height:29.6px;color:#333}
.about-copy p+p{margin-top:30px}

/* services */
.services-bg{left:0;top:1461px;width:1200px;height:860px;background:var(--soft);clip-path:polygon(0 0,100% 0,100% 73%,50% 97%,0 73%)}
.services-lead{left:230px;top:1622px;width:740px;text-align:center;font-size:14px;line-height:25px;color:#333}
.service-card{top:1702px;width:281px;height:380px;filter:drop-shadow(0 2px 6px rgba(0,0,0,.15))}
.service-card .card-body{width:100%;height:100%;background:var(--white);clip-path:polygon(0 0,100% 0,100% 86%,50% 100%,0 86%);padding:6px 6px 0;text-align:center}
.service-photo{width:100%;height:199px}
.service-name{margin-top:20px;font-family:"Montserrat",sans-serif;font-weight:600;font-size:17px;color:#222;letter-spacing:.3px}
.service-text{margin:8px auto 0;width:230px;font-size:13px;line-height:25px;color:#555}
.service-link{display:inline-block;margin-top:8px;font-family:"Montserrat",sans-serif;font-weight:600;font-size:12.5px;color:var(--orange);text-decoration:underline}

/* testimonials */
.avatar{border-radius:50%}
.client-name{left:0;top:2658px;width:1200px;text-align:center;font-family:"Montserrat",sans-serif;font-weight:600;font-size:20px;color:#222;letter-spacing:.4px}
.client-place{left:0;top:2693px;width:1200px;text-align:center;font-family:"Montserrat",sans-serif;font-weight:600;font-size:11px;color:#333}
.stars{left:0;top:2712px;width:1200px;text-align:center;color:var(--orange-2);font-size:30px;letter-spacing:2px}
.quote-text{left:255px;top:2760px;width:690px;text-align:center;font-size:14px;line-height:26px;color:#333}
.quote-mark{font-family:Georgia,serif;font-size:250px;line-height:1;color:#dcdcdc;font-weight:700}
.dot{width:13px;height:13px;border-radius:50%;background:#d5dcef}

/* contact */
.contact-bg{left:0;top:2977px;width:1200px;height:905px;background:linear-gradient(180deg,#e8862a 0%,#ef9233 45%,#e0802a 100%)}
.contact-title{left:0;top:3083px;width:1200px;text-align:center;font-family:"Montserrat",sans-serif;font-weight:700;font-size:34px;color:var(--white);letter-spacing:.6px}
.field{border:2px solid var(--white);color:var(--white);font-family:"Montserrat",sans-serif;font-weight:500;font-size:14px;padding:22px 0 0 17px}

/* footer */
.footer-title{top:3900px;font-family:"Montserrat",sans-serif;font-weight:500;font-size:20px;color:var(--white);letter-spacing:.3px}
.footer-list{top:3944px;list-style:none;font-size:14px;color:#e6e6e6}
.footer-list li{height:34.3px;display:flex;align-items:flex-start;gap:10px}
.footer-list svg{margin-top:3px;flex:none}
.contact-row{left:858px;display:flex;gap:16px;align-items:flex-start;font-size:14px;line-height:24px;color:#e6e6e6}
.contact-icon{width:30px;height:30px;border-radius:50%;background:var(--white);display:flex;align-items:center;justify-content:center;flex:none}
.footer-rule{left:110px;top:4147px;width:980px;height:1px;background:#9a9a9a}
.copyright{left:0;top:4184px;width:1200px;text-align:center;font-family:"Montserrat",sans-serif;font-size:14px;font-weight:500;color:var(--white)}
</style>
</head>
<body>

<!-- header -->
<div class="abs topbar"></div>
<div class="abs brand"><span class="brand-mark"></span><span>Fenwick Grading LTD</span></div>
<div class="abs nav" style="left:287px">HOME</div>
<div class="abs nav" style="left:373px">ABOUT</div>
<div class="abs nav" style="left:467px">IRRIGATION</div>
<div class="abs nav" style="left:594px">LANDSCAPE LIGHTING</div>
<div class="abs nav" style="left:804px">MORE &#8964;</div>
<div class="abs phone-badge">
  <svg width="24" height="24" viewBox="0 0 24 24"><path fill="#fff" d="M6.6 10.8a15.1 15.1 0 0 0 6.6 6.6l2.2-2.2a1 1 0 0 1 1-.25 11.4 11.4 0 0 0 3.6.57 1 1 0 0 1 1 1V20a1 1 0 0 1-1 1A17 17 0 0 1 3 4a1 1 0 0 1 1-1h3.5a1 1 0 0 1 1 1c0 1.25.2 2.45.57 3.57a1 1 0 0 1-.25 1z"/></svg>
</div>
<div class="abs phone-label">PHONE NUMBER</div>
<div class="abs phone-number">+1 555 010 7788</div>

<!-- hero -->
<div class="abs hero-photo" role="img" aria-label="Night photo of a lit brick garden path with bollard lights beside green lawn"></div>
<div class="abs hero-title">
  <span class="hl">HOMEOWNERS</span> WHO WANT GREEN GRASS AND <span class="hl">BEAUTIFUL</span><br>
  <span class="hl">GARDENS</span>. BEAUTIFUL LANDSCAPE <span class="hl">LIGHTING</span>
</div>
<div class="abs btn" style="left:474px;top:357px;width:254px;height:59px">GET STARTED</div>
<svg class="abs" style="left:0;top:600px" width="1200" height="220" viewBox="0 600 1200 220">
  <polygon fill="var(--orange)" points="108,625 600,782 1092,622 600,802"/>
</svg>

<!-- about -->
<div class="abs about-photo" role="img" aria-label="Modern house at dusk with garden lighting under a blue sky"></div>
<svg class="abs" style="left:104px;top:907px" width="460" height="478"><polygon points="6,6 454,6 230,471" fill="none" stroke="var(--orange)" stroke-width="2"/></svg>
<div class="abs section-mark" style="left:613px;top:872px"></div>
<div class="abs section-title" style="left:599px;top:904px"><span class="hl">ABOUT FENWICK</span> GRADING</div>
<div class="abs about-copy">
  <p>Excepteur sint occaecat cupidatat non proident, sunt in culpa qui officia nostrud exercitation ullamco laboris nisi deserunt id aborum.Quis autem vel eum iure reprehenderit qui in ea voltate velit esse quam nihil molestiae conseatur, quo voluptas velit pariatur.Duis aute irure dolor in reprehenderit in voluptate magni dolores velit esse cillum dolore eu fugiat nulla pariatur.</p>
  <p>SInt occaecat cupidatat non proident, sunt in culpa qui officia nostrud exercitation ullamco laboris nisi deserunt id aborum.Quis autem vel eum iure reprehenderit qui in ea voltate velit esse quam nihil molestiae conseatur, quo voluptas velit pariatur.</p>
</div>
<div class="abs btn" style="left:599px;top:1316px;width:258px;height:59px">READ MORE</div>

<!-- services -->
<div class="abs services-bg"></div>
<div class="abs section-mark" style="left:593px;top:1523px"></div>
<div class="abs section-title" style="left:0;top:1562px;width:1200px;text-align:center"><span class="hl">OUR</span> SERVICES</div>
<div class="abs services-lead">Excepteur sint occaecat cupidatat non proident, sunt in culpa qui officia nostrud exercitation ullamco laboris nisi deserunt id laborum.</div>

<div class="abs service-card" style="left:110px"><div class="card-body">
  <div class="service-photo" role="img" aria-label="Lit stone water feature wall for a commercial landscape" style="background:linear-gradient(180deg,#2c2a22,#6e5a44 55%,#1c1a15)"></div>
  <div class="service-name">COMMERCIAL</div>
  <div class="service-text">Quis autem vel eum iure reprehene am nihil molestiae pariatur.</div>
  <a class="service-link">READ MORE</a>
</div></div>
<div class="abs service-card" style="left:459px"><div class="card-body">
  <div class="service-photo" role="img" aria-label="Residential home lit at night" style="background:linear-gradient(180deg,#0c1f5a,#2a3a70 50%,#6a5a40 75%,#1a1a1a)"></div>
  <div class="service-name">RESIDENTIAL</div>
  <div class="service-text">Uis autem vel eum iure reprehene am nihil molestiae pariatur.</div>
  <a class="service-link">READ MORE</a>
</div></div>
<div class="abs service-card" style="left:807px"><div class="card-body">
  <div class="service-photo" role="img" aria-label="Illuminated entrance walkway with landscape lighting" style="background:linear-gradient(180deg,#2a2f2a,#6a6458 45%,#c9b48a 60%,#222 100%)"></div>
  <div class="service-name">LANDSCAPE LIGHTING</div>
  <div class="service-text">Quis autem vel eum iure reprehene am nihil molestiae pariatur.</div>
  <a class="service-link">READ MORE</a>
</div></div>

<svg class="abs" style="left:0;top:2120px" width="1200" height="220" viewBox="0 2120 1200 220">
  <polygon fill="var(--orange)" points="108,2138 600,2298 1092,2136 600,2318"/>
</svg>
<div class="abs btn" style="left:474px;top:2135px;width:254px;height:61px">VIEW MORE</div>

<!-- testimonials -->
<div class="abs section-mark" style="left:593px;top:2374px"></div>
<div class="abs section-title" style="left:0;top:2414px;width:1200px;text-align:center"><span class="hl">WHAT CUSTOMER</span> SAYS</div>
<div class="abs avatar" role="img" aria-label="Customer portrait" style="left:534px;top:2501px;width:132px;height:132px;background:radial-gradient(circle,#f6c9a0,#f0a864)"></div>
<div class="abs avatar" role="img" aria-label="Customer portrait" style="left:127px;top:2576px;width:66px;height:66px;background:radial-gradient(circle,#f0d2c0,#d9a890)"></div>
<div class="abs avatar" role="img" aria-label="Customer portrait" style="left:1005px;top:2503px;width:46px;height:46px;background:radial-gradient(circle,#e9d6cc,#8a7a70)"></div>
<div class="abs" style="left:372px;top:2614px;width:13px;height:13px;border-radius:50%;background:var(--orange)"></div>
<div class="abs" style="left:887px;top:2576px;width:6px;height:6px;border-radius:50%;background:#777"></div>
<div class="abs quote-mark" style="left:150px;top:2638px">&ldquo;</div>
<div class="abs quote-mark" style="left:942px;top:2742px">&rdquo;</div>
<div class="abs client-name">DORIAN KESSLER</div>
<div class="abs client-place">United States</div>
<div class="abs stars">&#9733;&#9733;&#9733;&#9733;&#9733;</div>
<div class="abs quote-text">Itaque earum rerum hic tenetur a sapiente delectus, ut aut reiciendis voluptatibus maiores alias. Consequatur aut perferendis doloribus asperiores repellat.Et harum quidem rerum facilis est et expedita distinctio.</div>
<div class="abs" style="left:541px;top:2880px;display:flex;gap:8px">
  <span class="dot"></span><span class="dot"></span><span class="dot"></span><span class="dot" style="background:var(--orange)"></span><span class="dot"></span><span class="dot"></span>
</div>

<!-- contact -->
<div class="abs contact-bg" role="img" aria-label="Warm orange-toned photo of a lit garden walkway"></div>
<div class="abs section-mark" style="left:593px;top:3047px;background:var(--white)"></div>
<div class="abs contact-title">GET IN TOUCH WITH US</div>
<div class="abs field" style="left:121px;top:3167px;width:468px;height:61px">Name</div>
<div class="abs field" style="left:609px;top:3167px;width:469px;height:61px">Email</div>
<div class="abs field" style="left:121px;top:3244px;width:468px;height:61px">Phone number</div>
<div class="abs field" style="left:609px;top:3244px;width:469px;height:61px">Address</div>
<div class="abs field" style="left:121px;top:3322px;width:957px;height:129px">Address</div>
<div class="abs btn btn-light" style="left:499px;top:3518px;width:204px;height:60px">SUBMIT</div>

<!-- footer -->
<svg class="abs" style="left:0;top:3630px" width="1200" height="624" viewBox="0 3630 1200 624">
  <polygon fill="var(--white)" points="0,3850 596,3634 1200,3850 1200,4254 0,4254"/>
  <polygon fill="var(--orange)" points="0,3868 600,3654 1200,3868 1200,4254 0,4254"/>
  <polygon fill="var(--dark)" points="0,3876 600,3690 1200,3876 1200,4254 0,4254"/>
</svg>
<div class="abs brand" style="top:3950px;left:110px;width:230px;font-size:26px;line-height:32px"><span class="brand-mark"></span><span>Fenwick Grading LTD</span></div>

<div class="abs footer-title" style="left:406px">QUICK LINKS</div>
<ul class="abs footer-list" style="left:406px">
  <li><svg width="14" height="12" viewBox="0 0 14 12"><path d="M0 6h11M7 1l5 5-5 5" stroke="#fff" stroke-width="2" fill="none"/></svg>Home</li>
  <li><svg width="14" height="12" viewBox="0 0 14 12"><path d="M0 6h11M7 1l5 5-5 5" stroke="#fff" stroke-width="2" fill="none"/></svg>About</li>
  <li><svg width="14" height="12" viewBox="0 0 14 12"><path d="M0 6h11M7 1l5 5-5 5" stroke="#fff" stroke-width="2" fill="none"/></svg>Landscape Lighting</li>
  <li><svg width="14" height="12" viewBox="0 0 14 12"><path d="M0 6h11M7 1l5 5-5 5" stroke="#fff" stroke-width="2" fill="none"/></svg>Fiber Optic installation</li>
  <li><svg width="14" height="12" viewBox="0 0 14 12"><path d="M0 6h11M7 1l5 5-5 5" stroke="#fff" stroke-width="2" fill="none"/></svg>Contact Us</li>
</ul>

<div class="abs footer-title" style="left:657px">HELP LINKS</div>
<ul class="abs footer-list" style="left:657px">
  <li><svg width="14" height="12" viewBox="0 0 14 12"><path d="M0 6h11M7 1l5 5-5 5" stroke="#fff" stroke-width="2" fill="none"/></svg>FAQ</li>
  <li><svg width="14" height="12" viewBox="0 0 14 12"><path d="M0 6h11M7 1l5 5-5 5" stroke="#fff" stroke-width="2" fill="none"/></svg>Terms of use</li>
  <li><svg width="14" height="12" viewBox="0 0 14 12"><path d="M0 6h11M7 1l5 5-5 5" stroke="#fff" stroke-width="2" fill="none"/></svg>Privacy Policy</li>
  <li><svg width="14" height="12" viewBox="0 0 14 12"><path d="M0 6h11M7 1l5 5-5 5" stroke="#fff" stroke-width="2" fill="none"/></svg>Support Links</li>
  <li><svg width="14" height="12" viewBox="0 0 14 12"><path d="M0 6h11M7 1l5 5-5 5" stroke="#fff" stroke-width="2" fill="none"/></svg>Conditions</li>
</ul>

<div class="abs footer-title" style="left:858px">CONTACT US</div>
<div class="abs contact-row" style="top:3944px">
  <span class="contact-icon"><svg width="14" height="18" viewBox="0 0 14 18"><path d="M7 0a7 7 0 0 0-7 7c0 5 7 11 7 11s7-6 7-11a7 7 0 0 0-7-7zm0 9.5A2.5 2.5 0 1 1 7 4.5a2.5 2.5 0 0 1 0 5z" fill="#333"/></svg></span>
  <span>Fenwick Grading<br>United States</span>
</div>
<div class="abs contact-row" style="top:4012px">
  <span class="contact-icon"><svg width="16" height="16" viewBox="0 0 24 24"><path fill="#333" d="M6.6 10.8a15.1 15.1 0 0 0 6.6 6.6l2.2-2.2a1 1 0 0 1 1-.25 11.4 11.4 0 0 0 3.6.57 1 1 0 0 1 1 1V20a1 1 0 0 1-1 1A17 17 0 0 1 3 4a1 1 0 0 1 1-1h3.5a1 1 0 0 1 1 1c0 1.25.2 2.45.57 3.57a1 1 0 0 1-.25 1z"/></svg></span>
  <span>(555) 014-2297</span>
</div>
<div class="abs contact-row" style="top:4064px;font-size:13px">
  <span class="contact-icon"><svg width="16" height="12" viewBox="0 0 16 12"><rect width="16" height="12" rx="1" fill="#333"/><path d="M1 1l7 6 7-6" stroke="#fff" stroke-width="1.4" fill="none"/></svg></span>
  <span>fenwickgrading@mailbox-example.net</span>
</div>

<div class="abs footer-rule"></div>
<div class="abs copyright">Copyrights@2024.Fenwick Grading.All Rights Reserved</div>

</body>
</html>
```